Business Card & Letterhead Design

We a financial advice company based in Australia. We provide advice to wealthy farmers.

We are changing our business name FROM Brightvale Financial TO Brackenlow Wealth and we need a new letterhead and double sided business card design

Attached is designs from our previous branding (Brightvale Financial) as it includes all the details we require on the new Brackenlow Wealth business cards and letterhead.

Need extra days to review

```html
<!DOCTYPE html>
<html lang="en">
<head>
<meta charset="utf-8">
<title>Brackenlow Wealth — Business Card</title>
<link href="https://fonts.googleapis.com/css2?family=Mulish:wght@400;600;700&display=swap" rel="stylesheet">
<style>
  :root {
    --backdrop: #a7a7a7;
    --card-front: #f7f7f6;
    --card-back: #474747;
    --ink: #2f2f2f;
    --ink-soft: #5a5a5a;
    --rule: #3a3a3a;
    --emboss: #5e5e5e;
  }
  * { margin: 0; padding: 0; box-sizing: border-box; }
  html, body { width: 1200px; height: 857px; overflow: hidden; }
  body {
    background: var(--backdrop);
    font-family: "Mulish", sans-serif;
    display: flex;
    align-items: center;
    justify-content: center;
    gap: 56px;
  }
  .card {
    width: 525px;
    height: 300px;
    border-radius: 2px;
    position: relative;
    box-shadow: 0 10px 24px rgba(0,0,0,0.22);
  }
  .card--front { background: var(--card-front); color: var(--ink); display: flex; }
  .card--back { background: var(--card-back); display: flex; align-items: center; justify-content: center; }

  .brand { display: flex; flex-direction: column; align-items: center; gap: 12px; }
  .brand__mark {
    width: 46px; height: 46px; border-radius: 50%;
    border: 2px solid currentColor;
  }
  .brand__name { font-size: 22px; font-weight: 600; letter-spacing: 0.06em; text-transform: uppercase; white-space: nowrap; }
  .brand__tagline { font-size: 9.5px; font-weight: 600; letter-spacing: 0.28em; text-transform: uppercase; margin-top: -8px; white-space: nowrap; }

  .card--front .brand { width: 250px; justify-content: center; color: var(--ink); }
  .card--front .brand__name { font-size: 18px; }
  .card--front .brand__tagline { font-size: 7.5px; color: var(--ink-soft); }
  .card--back .brand { color: var(--emboss); }

  .divider { width: 1.5px; background: var(--rule); margin: 56px 0; flex: none; }

  .contact { padding: 58px 0 0 26px; font-size: 11.5px; color: var(--ink-soft); line-height: 1.45; white-space: nowrap; }
  .contact__name { font-size: 15px; font-weight: 700; color: var(--ink); letter-spacing: 0.04em; text-transform: uppercase; }
  .contact__role { margin-bottom: 12px; }
  .contact__address { margin-bottom: 12px; }
  .contact__list { list-style: none; }
  .contact__list li { display: flex; align-items: center; gap: 8px; }
  .contact__list svg { width: 10px; height: 10px; fill: var(--ink); flex: none; }
</style>
</head>
<body>
  <section class="card card--front" aria-label="Business card front">
    <div class="brand">
      <span class="brand__mark"></span>
      <span class="brand__name">Brackenlow Wealth</span>
      <span class="brand__tagline">Strategic Financial Advice</span>
    </div>
    <div class="divider"></div>
    <div class="contact">
      <p class="contact__name">Daniel Hartley</p>
      <p class="contact__role">Operational Manager</p>
      <p class="contact__address">P/14 Kestrel Orchard Road<br>Wattle Blvd, NSW 2650</p>
      <ul class="contact__list">
        <li><svg viewBox="0 0 10 10"><path d="M2 0.5l2 2-1 1.2c.6 1.3 1.6 2.3 2.9 2.9L7 5.6l2 2-1.3 1.9C4 9.2 .8 6 .5 2.3z"/></svg>+61 2 5550 1234</li>
        <li><svg viewBox="0 0 10 10"><path d="M2.5 0h5v10h-5zM3.5 1v7h3V1z"/></svg>+61 491 570 156</li>
        <li><svg viewBox="0 0 10 10"><path d="M0 2h10v6H0zM1 3l4 2.5L9 3v-.2H1z"/></svg>daniel.hartley@brackenlow.example</li>
        <li><svg viewBox="0 0 10 10"><circle cx="5" cy="5" r="4.5"/></svg>www.brackenlow.example</li>
      </ul>
    </div>
  </section>

  <section class="card card--back" aria-label="Business card back">
    <div class="brand">
      <span class="brand__mark"></span>
      <span class="brand__name">Brackenlow Wealth</span>
      <span class="brand__tagline">Strategic Financial Advice</span>
    </div>
  </section>
</body>
</html>
```